Kleine Werbebroschüre für Bauunternehmen (Deckblatt plus  1. und 2. Seite)
Kleine Werbebroschüre für Bauunternehmen (Deckblatt plus 1. und 2. Seite)
Zielgruppe
Private Bauherren, Familien
Aufgabenstellung
Guten Tag zusammen,
wir benötigen einen klein Broschüre für ein Bauunternehmen, welche angelehnt werden kann an das Design unserer Internetseite www.linden-steinbau.de. Die Broschüre soll nur aus einem Deckblatt und dann beim Aufklappen aus einer ersten und zweiten Seite bestehen, die Rückseite kann frei bleiben bzw. hier genügt ein kleiner farblicher Balken mit z. B. unseren Kontaktinformationen. Die Bilder, Logos und Texte, welche verarbeitet werden sollen, laden wir gerne über das Portal hoch. Zur ganz groben Orientierung haben wir ein Word Dokument angelegt und hochgeladen, das Hausbild auf dem Deckblatt muss nicht, aber kann eingebaut werden, es muss sich halt gut in das Gesamtbild einfügen. Wir wünschen uns eine modernes, hochwertiges und vertrauenserweckendes Design, die Website soll nur zur Orientierung gelten und Eure Kreativität nicht einschränken. Wir sind für alle Vorschläge offen. Wenn es fragen gibt, sind wir jederzeit für Euch ansprechbar.
Wir freuen uns auf Eure Vorschläge.
Jörg

```html
<!DOCTYPE html>
<html lang="de">
<head>
<meta charset="utf-8">
<title>Linden Steinbau – Rückseite</title>
<link href="https://fonts.googleapis.com/css2?family=Cabin:wght@400;600&display=swap" rel="stylesheet">
<style>
  :root {
    --navy: #4e5f7d;
    --steel: #a3aebf;
    --paper: #f6f7f3;
    --mist: #e6e8e7;
    --white: #ffffff;
    --photo-warm: #d9c4a4;
    --photo-cool: #b8c6d6;
  }
  html, body {
    margin: 0;
    padding: 0;
    overflow: hidden;
  }
  .page {
    position: relative;
    width: 848px;
    height: 1200px;
    overflow: hidden;
    font-family: "Cabin", sans-serif;
    background:
      linear-gradient(180deg, var(--mist) 0%, var(--paper) 30%, var(--paper) 72%, var(--mist) 92%, var(--paper) 100%);
  }
  .contact-band {
    position: absolute;
    left: 0;
    top: 463px;
    width: 848px;
    height: 274px;
    background: var(--navy);
  }
  .photo-frame {
    position: absolute;
    left: 34px;
    top: 0;
    width: 291px;
    height: 274px;
    background: var(--steel);
  }
  .photo-placeholder {
    position: absolute;
    left: 0;
    top: 40px;
    width: 291px;
    height: 193px;
    background: linear-gradient(135deg, #3a3d44 0%, var(--photo-cool) 35%, var(--photo-warm) 70%, #f2ede4 100%);
  }
  .contact-details {
    position: absolute;
    left: 340px;
    top: 36px;
    color: var(--white);
  }
  .company-name {
    margin: 0 0 18px;
    font-size: 20.5px;
    font-weight: 600;
    line-height: 1.2;
  }
  .address-lines,
  .online-lines {
    margin: 0;
    font-size: 16.5px;
    line-height: 19.8px;
    font-weight: 400;
  }
  .online-lines {
    margin-top: 20px;
  }
  .footer-url {
    position: absolute;
    right: 29px;
    top: 1165px;
    margin: 0;
    color: var(--navy);
    font-size: 16px;
  }
</style>
</head>
<body>
<main class="page">
  <section class="contact-band">
    <div class="photo-frame">
      <div class="photo-placeholder" role="img" aria-label="Foto: Berater bespricht mit einem jungen Paar Baupläne am Tisch"></div>
    </div>
    <div class="contact-details">
      <h2 class="company-name">Linden Steinbau - Inhaber Markus Linden</h2>
      <p class="address-lines">
        Am Lindenhang 7<br>
        35041 Talheim<br>
        Fon: (06431) - 52 17 300<br>
        Fax: (06431) - 52 17 310<br>
        Mobil: (0157) - 31 64 80 22
      </p>
      <p class="online-lines">
        E-Mail: info@linden-steinbau.de<br>
        www.linden-steinbau.de
      </p>
    </div>
  </section>
  <p class="footer-url">www.linden-steinbau.de</p>
</main>
</body>
</html>
```